Business cards for Zestcycle

We need a business card layout for our new bike and e-bike rental (we also sell used e-bikes and bike accessories). The logo already exists.

```html
<!DOCTYPE html>
<html lang="en">
<head>
<meta charset="utf-8">
<title>Zestcycle — Business Cards</title>
<link href="https://fonts.googleapis.com/css2?family=Lato:wght@400;700&display=swap" rel="stylesheet">
<style>
  :root {
    --backdrop: #1d1d1e;
    --card: #2b2829;
    --card-pattern: #333031;
    --teal: #52c4a3;
    --white: #ffffff;
    --rule: #5a5657;
  }
  * { margin: 0; padding: 0; box-sizing: border-box; }
  html, body {
    width: 1200px; height: 1108px; overflow: hidden;
    background: var(--backdrop);
    font-family: "Lato", Arial, sans-serif;
  }
  .sheet {
    position: relative; width: 1200px; height: 1108px;
    display: flex; justify-content: center; align-items: center; gap: 70px;
  }
  .card {
    position: relative; width: 400px; height: 640px;
    background: var(--card); border-radius: 24px; overflow: hidden;
  }
  .card-front {
    display: flex; flex-direction: column; align-items: center;
    padding-top: 86px; color: var(--white); text-align: center;
  }
  .brand-dot {
    width: 46px; height: 46px; border-radius: 50%;
    border: 3px solid var(--white);
  }
  .brand-name {
    margin-top: 18px; color: var(--teal);
    font-weight: 400; font-size: 66px; letter-spacing: 1px; line-height: 1;
  }
  .tagline { margin-top: 20px; font-weight: 700; font-size: 20px; }
  .person-name {
    margin-top: 44px; color: var(--teal);
    font-weight: 400; font-size: 24px; letter-spacing: 0.5px;
  }
  .person-role { margin-top: 2px; font-size: 17px; }
  .divider {
    margin-top: 12px; width: 190px; display: flex; align-items: center; gap: 6px;
  }
  .divider::before, .divider::after {
    content: ""; flex: 1; height: 1px; background: var(--rule);
  }
  .contact-icon { width: 20px; height: 20px; }
  .contact-list { margin-top: 10px; font-size: 18px; line-height: 1.35; list-style: none; }
  .address {
    margin-top: 14px; padding-top: 12px; width: 220px;
    border-top: 1px solid var(--rule);
    font-size: 18px; line-height: 1.35; font-style: normal;
  }
  .card-back { background: var(--card); }
  .back-pattern {
    position: absolute; inset: 0 0 180px 0;
    background: linear-gradient(160deg, var(--card-pattern), var(--card));
  }
  .back-name {
    position: absolute; left: 0; right: 0; bottom: 118px; text-align: center;
    color: var(--white); font-weight: 400; font-size: 64px; letter-spacing: 1px;
  }
</style>
</head>
<body>
<main class="sheet">
  <section class="card card-front">
    <div class="brand-dot"></div>
    <h1 class="brand-name">ZESTCYCLE</h1>
    <p class="tagline">ride easy, roll far</p>
    <h2 class="person-name">MARCUS HALE</h2>
    <p class="person-role">Managing Director</p>
    <div class="divider">
      <svg class="contact-icon" viewBox="0 0 20 20" aria-label="Phone">
        <circle cx="10" cy="10" r="10" fill="var(--teal)"/>
        <path d="M7 5.5c-.8.3-1.4 1.2-1.1 2.3.8 2.8 3.4 5.4 6.2 6.2 1.1.3 2-.3 2.3-1.1l-1.9-1.4-1.1.9c-1.2-.6-2.3-1.7-2.9-2.9l.9-1.1z" fill="var(--card)"/>
      </svg>
      <svg class="contact-icon" viewBox="0 0 20 20" aria-label="Email">
        <circle cx="10" cy="10" r="10" fill="var(--teal)"/>
        <rect x="5" y="6.5" width="10" height="7" fill="var(--card)"/>
        <path d="M5 6.5l5 4 5-4" stroke="var(--teal)" stroke-width="1" fill="none"/>
      </svg>
      <svg class="contact-icon" viewBox="0 0 20 20" aria-label="Website">
        <circle cx="10" cy="10" r="10" fill="var(--teal)"/>
        <circle cx="10" cy="10" r="5" fill="none" stroke="var(--card)" stroke-width="1.4"/>
        <path d="M5 10h10M10 5c-2 3-2 7 0 10M10 5c2 3 2 7 0 10" fill="none" stroke="var(--card)" stroke-width="1.2"/>
      </svg>
    </div>
    <ul class="contact-list">
      <li>444 555 7120</li>
      <li>hello@zestcycle.com</li>
      <li>www.zestcycle.com</li>
    </ul>
    <address class="address">38, Linden Lane,<br>Riverton, 40218</address>
  </section>

  <section class="card card-back">
    <div class="back-pattern" role="img" aria-label="Faint repeating pattern of the brand symbol"></div>
    <p class="back-name">ZESTCYCLE</p>
  </section>
</main>
</body>
</html>
```